Etikett für Rotweinflasche
Liebe farbkosmos Atelier, wir werden uns bei der endgültigen Etikettengestaltung (finale Größe + Rückseite) noch an Euch melden. Bitte sendet uns euren Kontakt an helga.brandt@morvelli.wine
Zielgruppe
Morvelli Italia ist ein exklusives Boutique-Weingut in Sizilien, das hochqualitative Spitzenweine in kleinen Mengen mit modernster Technologie und stets nachhaltig erzeugt. Wir hinterfragen sowohl in der Agronomie im Weingarten als auch in der Önologie im Weinkeller alle herrschenden Traditionen und trachten danach, stets das beste Endprodukt zu kreieren. Der vulkanische, kalkreiche Boden Siziliens sowie trockene, sonnenreiche und niederschlagsarme Vegetationsperioden sind unsere optimale Basis.
Zielgruppe: Internationale Genussmenschen jeglichen Alters, die sich bewusst auch höherpreisige Weine (um die €30+) gönnen , vor allem kunstaffine young professionals mit Qualitäts-& Nachhaltigkeitsanspruch
Aufgabenstellung
Das Etikett ist für Rotwein-Flaschen (Cabernet Sauvignon / Nero D'Avola / Frappato / Syrah / Cerasuolo / Petit Verdot / sowie einen Bourdeaux-Cuveè aus Cabernet Sauvignon und Petit Verdot) .
Die Flasche ist reinschwarz, sehr hochwertig und schwer.
Flaschenform: Bordeauxflasche siehe technisches Datenblatt
Sleeve über dem Korken: schwarz mit weißer Schrift wie bisher
Zu gestalten ist das Etikett der Vorderseite. Zumindest die jeweilige Rotwein-Sorte ist auch textlich darzustellen (zwecks Scannen mit Trubel-App)
Der Kreativität kann freien Lauf gelassen werden! Unterscheidbarkeit vom Markt ist explizit gewollt.
Unsere aktuellen Etiketten und Markenauftritt siehe: https://morvelli.wine/shop/

```html
<!DOCTYPE html>
<html lang="it">
<head>
<meta charset="utf-8">
<title>Cerasuolo – Etikett</title>
<link rel="stylesheet" href="https://fonts.googleapis.com/css2?family=Cormorant+Garamond:wght@400&display=swap">
<style>
  :root {
    --backdrop: #1e1e1e;
    --label-black: #0b0b0b;
    --label-edge: #151515;
    --type-silver: #c9c9c9;
    --bubble-rim: rgba(255,255,255,0.38);
    --fish-blue: #2a45d8;
    --fish-deep: #0d1a7a;
  }
  html, body {
    margin: 0;
    padding: 0;
    width: 1200px;
    height: 1187px;
    overflow: hidden;
    background: var(--backdrop);
  }
  .canvas {
    position: relative;
    width: 1200px;
    height: 1187px;
  }
  .label {
    position: absolute;
    left: 250px;
    top: 93px;
    width: 700px;
    height: 1000px;
    background: var(--label-black);
    box-shadow: inset 0 0 0 1px var(--label-edge);
  }
  .varietal {
    position: absolute;
    top: 118px;
    left: 0;
    width: 100%;
    margin: 0;
    text-align: center;
    font-family: "Cormorant Garamond", serif;
    font-weight: 400;
    font-size: 30px;
    letter-spacing: 0.62em;
    padding-left: 0.62em;
    box-sizing: border-box;
    color: var(--type-silver);
  }
  .bubble {
    position: absolute;
    left: 49px;
    top: 259px;
    width: 602px;
    height: 602px;
  }
</style>
</head>
<body>
  <main class="canvas">
    <section class="label">
      <h1 class="varietal">CERASUOLO</h1>
      <svg class="bubble" viewBox="0 0 602 602" xmlns="http://www.w3.org/2000/svg">
        <defs>
          <radialGradient id="bubble-glass" cx="50%" cy="50%" r="50%">
            <stop offset="0.82" stop-color="#000" stop-opacity="0"/>
            <stop offset="1" stop-color="#fff" stop-opacity="0.12"/>
          </radialGradient>
          <radialGradient id="fish-tone" cx="45%" cy="50%" r="55%">
            <stop offset="0" stop-color="var(--fish-blue)"/>
            <stop offset="0.7" stop-color="var(--fish-deep)"/>
            <stop offset="1" stop-color="var(--fish-deep)" stop-opacity="0"/>
          </radialGradient>
        </defs>
        <circle cx="301" cy="301" r="299" fill="url(#bubble-glass)" stroke="var(--bubble-rim)" stroke-width="2"/>
        <ellipse role="img" aria-label="Illustration eines blauen Mandarinfisches in der Glaskugel"
                 cx="290" cy="285" rx="270" ry="160" fill="url(#fish-tone)"/>
        <path d="M380 120 Q470 170 500 260" fill="none" stroke="rgba(255,255,255,0.18)" stroke-width="10" stroke-linecap="round"/>
      </svg>
    </section>
  </main>
</body>
</html>
```